Software Development Consulting Company Needs Business Card Design

We need a new business card design for our consultants at Kestrel Works (kestrelworks.example). We are a small firm that provides high-end software development and methodology consulting to medium to large enterprise IT organizations.

Our logo uses Futura for the font and we would like to stick with navy blue and canary yellow for the logo colors. Attached are normal and reversed versions of our logos in illustrator format.
Updates

Hi Everyone, Thank yo very much for your amazing design ideas. I have created a poll for this project and our employees will be voting on the design they wish to use. We will be making a decision this Wednesday (October 22nd). Thanks again, Dale Hartwick

Industry/Entity Type

Business

```html
<!DOCTYPE html>
<html lang="en">
<head>
<meta charset="utf-8">
<title>Kestrel Works – Business Card</title>
<link rel="stylesheet" href="https://fonts.googleapis.com/css2?family=Jost:wght@500&family=PT+Sans:wght@400;700&display=swap">
<style>
  :root {
    --navy: #1f4469;
    --canary: #f3e600;
    --paper: #ffffff;
    --ink: #1f4469;
    --grey-text: #4a4f57;
    --backdrop: #e9e9ee;
  }
  * { box-sizing: border-box; margin: 0; padding: 0; }
  html, body { width: 1200px; height: 980px; overflow: hidden; }
  body {
    background: var(--backdrop);
    font-family: "PT Sans", Arial, sans-serif;
    position: relative;
  }
  .card {
    position: absolute;
    left: 250px;
    width: 700px;
    height: 400px;
    background: var(--paper);
    border-radius: 28px;
    overflow: hidden;
    box-shadow: 0 6px 18px rgba(40, 50, 70, 0.18);
  }
  .card--front { top: 70px; }
  .card--back { top: 510px; }

  .card__band { position: absolute; inset: 0; width: 700px; height: 400px; }

  .brand {
    position: absolute;
    display: flex;
    align-items: center;
    gap: 14px;
    font-family: "Jost", Futura, sans-serif;
    font-weight: 500;
    color: var(--ink);
    text-transform: uppercase;
    white-space: nowrap;
  }
  .brand__dot {
    border-radius: 50%;
    background: var(--canary);
    border: 3px solid var(--navy);
    flex: none;
  }
  .card--front .brand { left: 0; right: 0; top: 70px; justify-content: center; font-size: 50px; letter-spacing: 5px; }
  .card--front .brand__dot { width: 18px; height: 18px; }

  .holder {
    position: absolute;
    left: 330px;
    top: 178px;
    color: var(--ink);
    font-size: 26px;
  }
  .holder__name { font-weight: 700; }
  .holder__title { font-weight: 400; font-size: 22px; color: var(--grey-text); }

  .contact {
    position: absolute;
    display: flex;
    align-items: center;
    gap: 8px;
    color: #ffffff;
    font-size: 17px;
    white-space: nowrap;
  }
  .contact svg { width: 16px; height: 16px; flex: none; }
  .contact--email { left: 34px; top: 268px; }
  .contact--phone { left: 34px; top: 305px; }
  .contact--web { left: 200px; top: 305px; }
  .contact--address { left: 34px; top: 342px; }

  .card--back .brand { left: 0; right: 0; top: 140px; justify-content: center; font-size: 62px; letter-spacing: 6px; }
  .card--back .brand__dot { width: 22px; height: 22px; }
  .site {
    position: absolute;
    left: 0; right: 0; top: 240px;
    text-align: center;
    font-family: "Jost", Futura, sans-serif;
    font-weight: 500;
    font-size: 22px;
    letter-spacing: 4px;
    color: var(--grey-text);
  }
</style>
</head>
<body>

<section class="card card--front" aria-label="Business card front">
  <svg class="card__band" viewBox="0 0 700 400" aria-hidden="true">
    <path d="M0,196 C205,216 480,286 660,400" fill="none" stroke="var(--canary)" stroke-width="4"/>
    <path d="M0,210 C200,230 470,300 640,400 L0,400 Z" fill="var(--navy)"/>
  </svg>

  <div class="brand"><span class="brand__dot"></span>Kestrel Works</div>

  <p class="holder"><span class="holder__name">Your Name,</span> <span class="holder__title">Title</span></p>

  <p class="contact contact--email">
    <svg viewBox="0 0 16 16" aria-hidden="true"><rect x="1" y="3" width="14" height="10" rx="1" fill="var(--canary)"/><path d="M1.5,3.5 L8,9 L14.5,3.5" fill="none" stroke="var(--navy)" stroke-width="1.4"/></svg>
    info@kestrelworks.example
  </p>
  <p class="contact contact--phone">
    <svg viewBox="0 0 16 16" aria-hidden="true"><circle cx="8" cy="8" r="7" fill="none" stroke="var(--canary)" stroke-width="1.6"/><path d="M5.5,4.5 L7,4.5 L7.5,6.5 L6.6,7.3 C7.2,8.6 7.8,9.2 8.9,9.7 L9.7,8.8 L11.5,9.3 L11.5,10.8 C8,11.3 5,8 5.5,4.5 Z" fill="var(--canary)"/></svg>
    012-555-0188
  </p>
  <p class="contact contact--web">
    <svg viewBox="0 0 16 16" aria-hidden="true"><g fill="none" stroke="var(--canary)" stroke-width="1.4"><circle cx="8" cy="8" r="6.8"/><ellipse cx="8" cy="8" rx="3" ry="6.8"/><path d="M1.2,8 H14.8 M2.5,4.5 H13.5 M2.5,11.5 H13.5"/></g></svg>
    www.kestrelworks.example
  </p>
  <p class="contact contact--address">
    <svg viewBox="0 0 16 16" aria-hidden="true"><path d="M8,15 C4,10 3,8 3,6 A5,5 0 0 1 13,6 C13,8 12,10 8,15 Z" fill="var(--canary)"/><circle cx="8" cy="6" r="1.8" fill="var(--navy)"/></svg>
    Lakeport, Ridgefield, IL
  </p>
</section>

<section class="card card--back" aria-label="Business card back">
  <div class="brand"><span class="brand__dot"></span>Kestrel Works</div>
  <p class="site">www.kestrelworks.example</p>
</section>

</body>
</html>
```